The Polish & Glow Studio Website Update

Hello. I am seeking to freshen up my website with a clean and easy feel that incorporates our modern chic style. Our services cater to mostly young professionals and modern moms.

We focus on natural nail care and gentle professional waxing. We are known for our cleanliness. Our clients like our current website, however I'm hoping to make it look even more professional and user friendly. Some clients have even said our current website feels welcoming, unlike other websites that in they feel give a snobbish vibe. I like clean lines, simple, fresh, and sometimes bold. Totally NOT a fan of whimsical.

I threw added an accent color to the color pallet...however it should be used in moderation. I am also open to other accent colors. I'd like the site to emphasize the Brazilian wax as much as nails, if not more than nail. The photos downloaded are just to give you a few images of who we are, however are not necessary. Current website www.thepolishandglowstudio.example

Target Market(s)

Females 30-55

Industry/Entity Type

Beauty Salon

Coding

Coded - Design and coding required

Number of Pages Required

5+ page

Font styles to use
Sans Serif

Colors
ffffff
1b1b1b
acd136
eeeeee
878787
c4c4c4
efefef
7f7f7f

Requirements
Must have
• Clean look
Nice to have
• Our logo
Should not have
• Whimsical

```html
<!DOCTYPE html>
<html lang="en">
<head>
<meta charset="utf-8">
<title>The Polish &amp; Glow Studio</title>
<link rel="stylesheet" href="https://fonts.googleapis.com/css2?family=Open+Sans:wght@300;400;600;700;800&display=swap">
<style>
:root{
  --white:#ffffff;
  --ink:#1b1b1b;
  --lime:#acd136;
  --lime-dark:#8fb021;
  --mist:#eeeeee;
  --steel:#878787;
  --silver:#c4c4c4;
  --paper:#efefef;
  --slate:#7f7f7f;
  --star:#d32323;
}
*{box-sizing:border-box;margin:0;padding:0}
html,body{width:749px;height:1200px;overflow:hidden}
body{font-family:"Open Sans",sans-serif;color:var(--ink);background:var(--white);position:relative}
.abs{position:absolute}
/* header */
.brand{left:100px;top:12px;font-weight:300;font-size:20px;line-height:1;color:var(--ink);letter-spacing:.2px}
.brand small{display:block;font-size:8px;letter-spacing:2px;margin-top:3px;color:var(--slate)}
.call{left:424px;top:18px;width:103px;height:23px;background:var(--steel);color:var(--white);font-size:8px;display:flex;align-items:center;justify-content:center;gap:5px}
.book{left:527px;top:18px;width:120px;height:23px;background:var(--lime);color:var(--white);font-size:8px;font-weight:700;display:flex;align-items:center;justify-content:center;gap:6px}
.nav{left:0;top:58px;width:749px;height:22px;background:var(--ink)}
.nav a{position:absolute;top:0;height:22px;line-height:22px;color:var(--white);font-size:7px;text-decoration:none}
.nav a.current{background:var(--lime);padding:0 9px;left:101px}
/* hero */
.hero{left:0;top:80px;width:749px;height:274px;background:linear-gradient(100deg,#46b3d8 0%,#7fd0ea 45%,#e8c3a6 70%,#d9a886 100%)}
.mission{left:101px;top:124px;width:232px}
.mission h1{font-weight:800;font-size:21px;letter-spacing:.3px;color:var(--ink)}
.mission p{font-size:7.4px;line-height:12px;margin-top:6px;text-align:justify;color:#222}
.more{left:104px;top:211px;width:64px;height:18px;background:var(--lime);color:var(--ink);font-size:6.5px;font-weight:700;display:flex;align-items:center;justify-content:center}
.arrow{top:205px;width:38px;height:38px;border-radius:50%;background:rgba(40,50,60,.6)}
.dots{left:336px;top:326px;display:flex;gap:11px;align-items:center}
.dots i{width:6px;height:6px;border-radius:50%;background:var(--white);display:block}
.dots i.on{width:9px;height:9px;background:none;border:1.5px solid var(--white)}
/* offers */
.sec-title{width:749px;text-align:center;font-size:14px;font-weight:400;letter-spacing:.3px}
.offer{top:399px;width:176px;height:134px;border:1px solid #ddd;overflow:hidden}
.offer .ph{position:absolute;inset:0}
.offer .label{position:absolute;font-weight:800;color:var(--ink)}
.tag{position:absolute;bottom:0;right:0;background:var(--lime);color:var(--white);font-size:5.5px;font-weight:700;padding:3px 6px}
/* products */
.band{left:0;top:553px;width:749px;height:215px;background:var(--steel)}
.seeall{left:350px;top:593px;width:48px;height:15px;background:var(--ink);color:var(--white);font-size:5.5px;font-weight:700;display:flex;align-items:center;justify-content:center}
.card{top:620px;width:131px;height:118px}
.card .price{position:absolute;right:0;top:0;background:rgba(40,40,40,.75);color:var(--white);font-size:10px;font-weight:600;padding:2px 4px}
.card .name{position:absolute;bottom:6px;width:100%;text-align:center;color:var(--white);font-size:6.5px;font-weight:700}
.card .rm{position:absolute;right:0;bottom:-11px;background:var(--lime);color:var(--ink);font-size:4.5px;font-weight:700;padding:2px 4px}
.nudge{top:664px;width:24px;height:24px;border-radius:50%;background:var(--mist)}
/* forms */
.lower{left:0;top:768px;width:749px;height:238px;background:var(--silver)}
.panel{top:784px;height:204px;background:var(--white)}
.panel h2{font-weight:400;font-size:14px}
.field{position:absolute;height:23px;border:1px solid #cfcfcf;font-size:6.5px;padding:0 8px;display:flex;align-items:center;justify-content:space-between;color:#444}
.send{left:305px;top:957px;width:51px;height:18px;background:var(--lime);font-size:8px;font-weight:700;display:flex;align-items:center;justify-content:center}
.review{left:385px;width:257px;height:48px;border:1px solid #d6d6d6}
.review .av{position:absolute;left:6px;top:7px;width:29px;height:29px;background:linear-gradient(135deg,#6b5a4a,#b99b7d)}
.review .who{position:absolute;left:45px;top:5px;font-size:6px;line-height:9px}
.review .who b{font-weight:600}
.stars{position:absolute;left:45px;top:25px;display:flex;gap:1px}
.stars i{width:10px;height:10px;background:var(--star);display:block}
.review p{position:absolute;left:115px;top:5px;width:136px;font-size:5.6px;line-height:8.5px;color:#555}
/* footer */
.foot{left:0;top:1006px;width:749px;height:194px;background:#000;color:var(--white)}
.foot h4{position:absolute;font-size:6.8px;font-weight:700;letter-spacing:.2px}
.foot ul{position:absolute;list-style:none;font-size:6px;line-height:12.2px;color:#ddd}
.fin{position:absolute;left:350px;width:132px;height:20px;background:#3a3a3a;font-size:6px;color:#bbb;padding-left:12px;display:flex;align-items:center}
.signup{position:absolute;left:350px;top:98px;width:132px;height:25px;background:var(--lime);color:var(--ink);font-size:9px;font-weight:700;display:flex;align-items:center;justify-content:center}
.social{position:absolute;top:109px;width:18px;height:18px;border-radius:50%}
</style>
</head>
<body>

<header>
  <div class="abs brand">The Polish &amp; Glow<small>STUDIO</small></div>
  <div class="abs call">
    <svg width="8" height="8" viewBox="0 0 24 24"><path fill="#fff" d="M6.6 10.8a15 15 0 006.6 6.6l2.2-2.2c.3-.3.7-.4 1-.2 1.1.4 2.3.6 3.6.6.6 0 1 .4 1 1V20c0 .6-.4 1-1 1A17 17 0 013 4c0-.6.4-1 1-1h3.5c.6 0 1 .4 1 1 0 1.3.2 2.5.6 3.6.1.3 0 .7-.2 1z"/></svg>
    (555) 014-2038
  </div>
  <div class="abs book">
    <svg width="8" height="8" viewBox="0 0 24 24"><rect x="3" y="5" width="18" height="16" rx="1" fill="none" stroke="#fff" stroke-width="2"/><path d="M3 10h18M8 3v4M16 3v4" stroke="#fff" stroke-width="2"/></svg>
    SCHEDULE ONLINE!
  </div>
  <nav class="abs nav">
    <a class="current" href="#">Home</a>
    <a href="#" style="left:160px">Schedule An Appointment</a>
    <a href="#" style="left:277px">Products &amp; Services</a>
    <a href="#" style="left:372px">Careers</a>
    <a href="#" style="left:435px">Specials</a>
    <a href="#" style="left:498px">About Us</a>
    <a href="#" style="left:565px">FAQ</a>
    <a href="#" style="left:611px">Contact Us</a>
  </nav>
</header>

<section>
  <div class="abs hero" role="img" aria-label="Woman relaxing by a pool in a turquoise swimsuit"></div>
  <div class="abs mission">
    <h1>OUR MISSION</h1>
    <p>To be the #1 nail and wax salon in the Brookfield, CT area, offering the most meticulous manicures, pedicures, and waxing service. We use superior products, advanced technique...</p>
  </div>
  <div class="abs more">READ MORE</div>
  <div class="abs arrow" style="left:-11px"><svg width="38" height="38"><path d="M22 13l-6 6 6 6" fill="none" stroke="#fff" stroke-width="2"/></svg></div>
  <div class="abs arrow" style="left:722px"><svg width="38" height="38"><path d="M16 13l6 6-6 6" fill="none" stroke="#fff" stroke-width="2"/></svg></div>
  <div class="abs dots"><i></i><i class="on"></i><i></i><i></i><i></i></div>
</section>

<section>
  <h2 class="abs sec-title" style="top:370px">SPECIAL OFFERS</h2>
  <div class="abs offer" style="left:101px">
    <div class="ph" role="img" aria-label="Hands with pink french manicure" style="background:linear-gradient(90deg,#ffffff 35%,#f1d2c4 70%,#e6b8a6)"></div>
    <div class="label" style="left:10px;top:35px;font-size:9.5px;line-height:11px">SENIOR<br>DISCOUNT</div>
    <div class="abs" style="left:10px;top:59px;font-size:6px;line-height:9px">Tuesdays &amp;<br>Wednesdays</div>
    <div class="abs" style="left:10px;top:80px;font-size:16px;font-weight:700;color:var(--lime)">15%</div>
    <div class="abs" style="left:12px;top:99px;font-size:8px;font-weight:700">OFF</div>
  </div>
  <div class="abs offer" style="left:287px">
    <div class="ph" role="img" aria-label="Woman receiving a chemical peel facial" style="background:linear-gradient(120deg,#f4f4f0 30%,#f2ead0 55%,#f5d24a)"></div>
    <div class="label" style="left:12px;top:92px;font-size:9.5px">CHEMICAL PEEL</div>
    <div class="abs" style="left:12px;top:105px;font-size:15px;font-weight:700;color:var(--lime)">$55 <span style="font-size:8px;color:var(--ink)">OFF</span></div>
    <div class="tag">LIMITED TIME OFFER</div>
  </div>
  <div class="abs offer" style="left:472px">
    <div class="ph" role="img" aria-label="Hands with dark patterned nail art" style="background:linear-gradient(120deg,#c89a80,#d9b29c 50%,#b4866d)"></div>
    <div class="abs" style="left:0;top:85px;width:51px;height:49px;background:var(--lime);color:var(--ink);text-align:center;padding-top:3px">
      <div style="font-size:9px;font-weight:800">UPTO</div>
      <div style="font-size:15px;font-weight:700;color:var(--white);line-height:17px">25%</div>
      <div style="font-size:8px;font-weight:700;color:#5a6b20">OFF</div>
    </div>
    <div class="tag">SELECTED SERVICES</div>
  </div>
</section>

<section>
  <div class="abs band"></div>
  <h2 class="abs sec-title" style="top:567px;color:var(--white)">PRODUCTS &amp; SERVICES</h2>
  <div class="abs seeall">SEE ALL &raquo;</div>
  <div class="abs nudge" style="left:53px"><svg width="24" height="24"><path d="M14 7l-5 5 5 5" fill="none" stroke="#888" stroke-width="1.4"/></svg></div>
  <div class="abs nudge" style="left:670px"><svg width="24" height="24"><path d="M10 7l5 5-5 5" fill="none" stroke="#888" stroke-width="1.4"/></svg></div>

  <div class="abs card" style="left:101px"><div role="img" aria-label="Manicured hands on pink petals" style="position:absolute;inset:0;background:linear-gradient(135deg,#e9a7b9,#f5e2dc 60%,#8a6a70)"></div><span class="price">$24</span><span class="name">SIGNATURE MANICURE</span><span class="rm">READ MORE &rsaquo;</span></div>
  <div class="abs card" style="left:239px"><div role="img" aria-label="Facial mask being applied" style="position:absolute;inset:0;background:linear-gradient(135deg,#aeb7c1,#e3e6e3 55%,#6d6f70)"></div><span class="price">$35</span><span class="name">SIGNATURE FACIAL</span><span class="rm">READ MORE &rsaquo;</span></div>
  <div class="abs card" style="left:378px"><div role="img" aria-label="Spa pedicure with flower petals" style="position:absolute;inset:0;background:linear-gradient(160deg,#e7c7b6,#f1d7c8 50%,#9b6a3c)"></div><span class="price">$40</span><span class="name">SPA PEDICURE</span><span class="rm">READ MORE &rsaquo;</span></div>
  <div class="abs card" style="left:517px"><div role="img" aria-label="Hands with colourful painted nails" style="position:absolute;inset:0;background:linear-gradient(135deg,#8a6a55,#e8d2c0 50%,#f3e7dc)"></div><span class="price">$20</span><span class="name">SIGNATURE MANICURE</span><span class="rm">READ MORE &rsaquo;</span></div>
</section>

<section>
  <div class="abs lower"></div>
  <div class="abs panel" style="left:101px;width:269px">
    <h2 class="abs" style="left:49px;top:13px">Schedule An Appointment</h2>
    <div class="abs" style="left:49px;top:36px;width:173px;height:1px;background:var(--ink)"></div>
  </div>
  <div class="field" style="left:117px;top:834px;width:115px">Name</div>
  <div class="field" style="left:241px;top:834px;width:115px">E mail</div>
  <div class="field" style="left:117px;top:864px;width:115px">Phone</div>
  <div class="field" style="left:241px;top:864px;width:115px">Select City <svg width="8" height="6"><path d="M1 1l3 3 3-3" fill="none" stroke="#333" stroke-width="1.2"/></svg></div>
  <div class="field" style="left:117px;top:894px;width:115px">Date <svg width="8" height="8" viewBox="0 0 24 24"><rect x="3" y="5" width="18" height="16" fill="none" stroke="#333" stroke-width="2"/><path d="M3 10h18M8 3v4M16 3v4" stroke="#333" stroke-width="2"/></svg></div>
  <div class="field" style="left:241px;top:894px;width:115px;height:52px;align-items:flex-start;padding-top:7px">Message</div>
  <div class="field" style="left:117px;top:924px;width:115px">Time <svg width="8" height="8" viewBox="0 0 24 24"><circle cx="12" cy="12" r="9" fill="none" stroke="#333" stroke-width="2.4"/><path d="M12 7v5h4" fill="none" stroke="#333" stroke-width="2.4"/></svg></div>
  <div class="abs send">SEND &raquo;</div>

  <div class="abs panel" style="left:378px;width:270px">
    <div class="abs" style="left:10px;top:13px;font-size:13px;font-weight:700">Ratewell <span style="font-weight:400;font-size:10px">Reviews</span></div>
    <svg class="abs" style="left:244px;top:14px" width="18" height="10"><path d="M5 1L1 5l4 4M13 1l4 4-4 4" fill="none" stroke="#777" stroke-width="1.2"/></svg>
  </div>
  <div class="abs review" style="top:822px">
    <div class="av" role="img" aria-label="Reviewer photo"></div>
    <div class="who"><b>Dana L.</b><br>Fairview, CT</div>
    <div class="stars"><i></i><i></i><i></i><i></i><i></i></div>
    <p>With unwavering patronage all due to Marisa's meticulous attention to detail and diligent sanitation processes, I'm now a regular now at The Polish &amp; Glow Studio.</p>
  </div>
  <div class="abs review" style="top:877px">
    <div class="av" role="img" aria-label="Reviewer photo"></div>
    <div class="who"><b>Rosa T.</b><br>Millbrook, CT</div>
    <div class="stars"><i></i><i></i><i></i><i></i><i></i></div>
    <p>I have been getting my nails done in different salons for over 18 years. During most of those 18 years I had acrylic nails. I am so happy to have found Marisa and her staff.</p>
  </div>
  <div class="abs review" style="top:931px">
    <div class="av" role="img" aria-label="Reviewer photo"></div>
    <div class="who"><b>Jen P.</b><br>Fairview, CT</div>
    <div class="stars"><i></i><i></i><i></i><i></i><i></i></div>
    <p>This place a fabulous! Very clean, they even ask if you want to keep the nail file they use for you because they use a new one for every single person!</p>
  </div>
</section>

<footer class="abs foot">
  <h4 style="left:101px;top:22px">CONTACT US</h4>
  <ul style="left:101px;top:36px">
    <li>The Polish &amp; Glow Studio</li><li>42 Linden Street</li><li>Brookfield, CT 06000</li><li>ph: (555) 014-2038</li>
  </ul>
  <h4 style="left:222px;top:22px">MENU</h4>
  <ul style="left:223px;top:36px">
    <li>Home</li><li>Schedule An Appointment</li><li>Products and Services</li><li>Careers</li><li>Specials</li><li>About Us</li><li>FAQ</li><li>Contact Us</li>
  </ul>
  <h4 style="left:349px;top:22px">NEWSLETTER SIGNUP!</h4>
  <div class="fin" style="top:44px">Name</div>
  <div class="fin" style="top:71px">E mail id</div>
  <div class="signup">SIGNUP!</div>
  <div class="abs" style="left:519px;top:36px;font-size:18px;font-weight:300;line-height:1;color:var(--white)">The Polish &amp; Glow<div style="font-size:8px;letter-spacing:2px;text-align:right;margin-top:3px">STUDIO</div></div>
  <h4 style="left:562px;top:96px">FOLLOW US ON</h4>
  <span class="social" style="left:545px;background:#3b5998"></span>
  <span class="social" style="left:569px;background:#1da1f2"></span>
  <span class="social" style="left:593px;background:#2a7bb0"></span>
  <span class="social" style="left:616px;background:#f26522"></span>
  <div class="abs" style="left:101px;top:160px;width:547px;height:1px;background:#333"></div>
  <div class="abs" style="left:543px;top:172px;font-size:5.5px;color:#aaa">Copyrights @ 2016 All Rights Reserved</div>
</footer>

</body>
</html>
```